NZ First of it's kind solutions directory and marketplace for busy Mums needs a business card design

We need a business card design for our new nationwide business in NZ (long term plans to go global). We provide solutions to the everyday challenges that busy Mums face by connecting them with quality communities and suppliers of carefully selected, relevant products and services. We sell direct via our online marketplace. The final design should communicate our values of inclusivity, quality and smart solutions. Colours should incorporate our logo colour palette of #477077 and #6ba8b2. Our website is at https://www.brightnestmums.example

Target Market(s)

busy Mums, Age 28 – 50, female, income over $100K, location main centres NZ primarily but NZ wide. Is likely juggling work or career with a young family. Probably had hobbies which have fallen by the wayside.
-Wants to succeed in her chosen career without compromising on family life
-to successfully juggle her career without feeling like she is compromising her children
- Is time poor, something always has to give and it’s generally her health (she’ll stay up late, get stressed)
- probably ex corporate or professional career. Has discretional income

Industry/Entity Type

Business

Contact Information for Business Card

Lena Forbisher, Founder, BrightNestMums.example (Strapline Tap; Gather; Sorted), 47 Kowhai Terrace, Ellerslie, Auckland 1051, New Zealand. Mob: 021 483 517 Ph: +64 (0)9 571 4860

Font styles to use
Other font styles liked:
• Raleway, and/or Architects Daughter

Colors
00a990
33b8a4
86cfc6
cfeae6

Requirements
Must have
• the above details, streamline. the logo and colours associated with those logos
Should not have
• foil or metallic colours

```html
<!DOCTYPE html>
<html lang="en">
<head>
<meta charset="utf-8">
<title>BrightNestMums – Business Card</title>
<link rel="stylesheet" href="https://fonts.googleapis.com/css2?family=Nunito:wght@800&family=Roboto:wght@400&family=Roboto+Condensed:ital,wght@0,400;1,400&display=swap">
<style>
  :root {
    --brand-dark: #477077;
    --brand-light: #6ba8b2;
    --ink: #3b4446;
    --paper: #fbfbfb;
    --backdrop: #dcdcdc;
    --watermark: #b7c3c5;
    --card-shadow: rgba(0, 0, 0, 0.28);
  }
  * { box-sizing: border-box; margin: 0; padding: 0; }
  html, body { width: 1200px; height: 576px; overflow: hidden; }
  body { background: var(--backdrop); position: relative; }

  .card {
    position: absolute;
    top: 138px;
    width: 484px;
    height: 294px;
    background: var(--paper);
    border-radius: 14px;
    box-shadow: 2px 3px 5px var(--card-shadow);
    overflow: hidden;
  }
  .card--front { left: 82px; }
  .card--back { left: 602px; }

  /* Front */
  .front-mark {
    position: absolute;
    left: 50%;
    top: 58px;
    width: 56px;
    height: 56px;
    margin-left: -28px;
    border-radius: 50%;
    background: var(--brand-dark);
  }
  .front-name {
    position: absolute;
    left: 0; right: 0;
    top: 162px;
    text-align: center;
    font-family: "Nunito", sans-serif;
    font-weight: 800;
    font-size: 34px;
    letter-spacing: -0.5px;
    color: var(--brand-dark);
  }
  .strapline {
    position: absolute;
    left: 0; right: 0;
    top: 214px;
    text-align: center;
    font-family: "Roboto", sans-serif;
    font-size: 10px;
    letter-spacing: 3.4px;
    color: var(--ink);
  }
  .strapline .divider { color: var(--brand-light); margin: 0 6px; }

  /* Back */
  .watermark-disc {
    position: absolute;
    left: 302px;
    top: 174px;
    width: 208px;
    height: 208px;
    border-radius: 50%;
    background: var(--watermark);
    opacity: 0.75;
  }
  .person { position: absolute; left: 22px; top: 43px; }
  .person-name {
    font-family: "Nunito", sans-serif;
    font-weight: 800;
    font-size: 19px;
    color: var(--brand-dark);
  }
  .person-role {
    font-family: "Roboto Condensed", sans-serif;
    font-style: italic;
    font-size: 12px;
    color: var(--ink);
    margin-top: 1px;
  }
  .back-brand {
    position: absolute;
    right: 20px;
    top: 52px;
    display: flex;
    align-items: center;
    gap: 7px;
  }
  .back-brand .brand-dot {
    width: 24px; height: 24px;
    border-radius: 50%;
    background: var(--brand-dark);
  }
  .back-brand .brand-name {
    font-family: "Nunito", sans-serif;
    font-weight: 800;
    font-size: 22px;
    letter-spacing: -0.3px;
    color: var(--brand-dark);
  }
  .address {
    position: absolute;
    left: 26px;
    top: 154px;
    font-family: "Roboto Condensed", sans-serif;
    font-size: 12.5px;
    line-height: 18px;
    color: var(--ink);
    font-style: normal;
  }
  .contact-list {
    position: absolute;
    left: 24px;
    top: 203px;
    list-style: none;
    font-family: "Roboto Condensed", sans-serif;
    font-size: 12.5px;
    line-height: 18px;
    color: var(--ink);
  }
  .contact-list li { display: flex; align-items: center; gap: 10px; }
  .contact-list svg { width: 12px; height: 12px; flex: none; fill: var(--brand-dark); }
</style>
</head>
<body>

<section class="card card--front" aria-label="Card front">
  <div class="front-mark" aria-hidden="true"></div>
  <div class="front-name">BrightNestMums</div>
  <div class="strapline">TAP<span class="divider">|</span>GATHER<span class="divider">|</span>SORTED</div>
</section>

<section class="card card--back" aria-label="Card back">
  <div class="watermark-disc" aria-hidden="true"></div>

  <div class="person">
    <div class="person-name">Lena Forbisher</div>
    <div class="person-role">Founder</div>
  </div>

  <div class="back-brand">
    <span class="brand-dot" aria-hidden="true"></span>
    <span class="brand-name">BrightNestMums</span>
  </div>

  <address class="address">
    47 Kowhai Terrace, Ellerslie,<br>
    Auckland 1051, New Zealand
  </address>

  <ul class="contact-list">
    <li>
      <svg viewBox="0 0 12 12" aria-hidden="true"><rect x="3" y="0.5" width="6" height="11" rx="1.2"/><rect x="4" y="2" width="4" height="7" fill="#fbfbfb"/></svg>
      021 483 517
    </li>
    <li>
      <svg viewBox="0 0 12 12" aria-hidden="true"><path d="M1 4 Q1 1.5 6 1.5 Q11 1.5 11 4 L9 5 L8 3.6 L4 3.6 L3 5 Z"/><rect x="2" y="6" width="8" height="5" rx="1"/></svg>
      +64 (0)9 571 4860
    </li>
    <li>
      <svg viewBox="0 0 12 12" aria-hidden="true"><rect x="0.5" y="2.5" width="11" height="7.5" rx="0.8"/><path d="M1 3 L6 7 L11 3" stroke="#fbfbfb" stroke-width="1" fill="none"/></svg>
      www.BrightNestMums.example
    </li>
    <li>
      <svg viewBox="0 0 12 12" aria-hidden="true"><circle cx="6" cy="6" r="5.5"/><path d="M0.5 6 H11.5 M6 0.5 V11.5 M6 0.5 Q2.5 6 6 11.5 M6 0.5 Q9.5 6 6 11.5" stroke="#fbfbfb" stroke-width="0.8" fill="none"/></svg>
      lena@brightnestmums.example
    </li>
  </ul>
</section>

</body>
</html>
```